Birchline Septic Solutions

Would like to see some single sided ones but would also like to see some double sided with one sided only being the logo. Owners name is Colin Vandro. Phone number is 555-214-0387
Services are pumping, inspections, installs, and repairs

Contact Information for Business Card

555-241-0387 Colin Vandro Maple Hollow, OH

```html
<!DOCTYPE html>
<html lang="en">
<head>
<meta charset="utf-8">
<title>Birchline Septic Solutions – Business Card</title>
<link href="https://fonts.googleapis.com/css2?family=Open+Sans:wght@400;600;700;800&display=swap" rel="stylesheet">
<style>
  :root {
    --page-bg: #222222;
    --card-bg: #1e1e22;
    --ink-light: #ffffff;
    --accent-teal: #26c1bb;
    --front-mark: #111113;
    --divider: #bdbdbd;
  }
  * { box-sizing: border-box; margin: 0; padding: 0; }
  html, body {
    width: 1200px; height: 779px; overflow: hidden;
    background: var(--page-bg);
    font-family: "Open Sans", Arial, sans-serif;
  }
  .sheet {
    width: 1200px; height: 779px;
    display: flex; flex-direction: column;
    align-items: center; justify-content: center; gap: 28px;
  }
  .card {
    position: relative;
    width: 600px; height: 343px;
    background: var(--card-bg);
    overflow: hidden;
    box-shadow: 0 6px 18px rgba(0,0,0,0.45);
  }

  /* Front: logo only */
  .card-front {
    display: flex; align-items: center; justify-content: center;
  }
  .front-wordmark {
    display: flex; align-items: center; gap: 14px;
    color: var(--front-mark);
    font-weight: 800; font-size: 26px; letter-spacing: 1px;
    text-transform: uppercase; white-space: nowrap;
  }
  .front-wordmark .mark-dot {
    flex: none; width: 26px; height: 26px; border-radius: 50%;
    background: var(--front-mark);
  }

  /* Back: contact side */
  .brand-block {
    position: absolute; left: 70px; top: 118px; width: 230px;
    display: flex; align-items: center; gap: 10px;
    color: var(--ink-light);
    font-weight: 800; font-size: 22px; line-height: 1.1;
    text-transform: uppercase;
  }
  .brand-block .mark-dot {
    flex: none; width: 22px; height: 22px; border-radius: 50%;
    background: var(--ink-light);
  }
  .contact-divider {
    position: absolute; left: 318px; top: 70px;
    width: 1px; height: 150px; background: var(--divider);
  }
  .contact-block {
    position: absolute; left: 345px; top: 92px;
    color: var(--ink-light);
  }
  .contact-name {
    font-weight: 700; font-size: 30px; line-height: 1.1;
  }
  .contact-name .first { color: var(--accent-teal); }
  .contact-city {
    font-size: 16px; margin-top: 4px;
  }
  .contact-phone {
    display: flex; align-items: center; gap: 8px;
    font-size: 16px; margin-top: 4px; padding-left: 8px;
  }
  .contact-phone svg { width: 14px; height: 14px; }

  .services-band {
    position: absolute; left: 0; right: 0; top: 276px; height: 36px;
    background: var(--accent-teal);
    display: flex; align-items: center; justify-content: center; gap: 14px;
    color: var(--ink-light); font-size: 16px;
  }
  .services-band .bullet {
    width: 9px; height: 9px; border-radius: 50%; background: var(--ink-light);
  }
  .services-tag {
    position: absolute; left: 275px; top: 250px;
    padding: 3px 16px;
    background: var(--accent-teal);
    border: 1.5px solid var(--ink-light);
    border-radius: 50%;
    color: var(--ink-light);
    font-weight: 600; font-size: 14px; letter-spacing: 0.5px;
  }
</style>
</head>
<body>
<main class="sheet">
  <section class="card card-front" aria-label="Card front">
    <div class="front-wordmark">
      <span class="mark-dot"></span>
      <span>Birchline Septic Solutions</span>
    </div>
  </section>

  <section class="card card-back" aria-label="Card back">
    <div class="brand-block">
      <span class="mark-dot"></span>
      <span>Birchline Septic Solutions</span>
    </div>

    <div class="contact-divider"></div>

    <div class="contact-block">
      <p class="contact-name"><span class="first">Colin</span> Vandro</p>
      <p class="contact-city">Maple Hollow, OH</p>
      <p class="contact-phone">
        <svg viewBox="0 0 24 24" aria-hidden="true"><path fill="#26c1bb" d="M6.6 10.8a15.1 15.1 0 0 0 6.6 6.6l2.2-2.2a1 1 0 0 1 1-.25 11.4 11.4 0 0 0 3.6.57 1 1 0 0 1 1 1V20a1 1 0 0 1-1 1A17 17 0 0 1 3 4a1 1 0 0 1 1-1h3.5a1 1 0 0 1 1 1c0 1.250.2 2.45.57 3.57a1 1 0 0 1-.25 1z"/></svg>
        555-241-0387
      </p>
    </div>

    <span class="services-tag">SERVICES</span>
    <div class="services-band">
      <span class="bullet"></span><span>Pumping</span>
      <span class="bullet"></span><span>Inspections</span>
      <span class="bullet"></span><span>Installs</span>
      <span class="bullet"></span><span>And Repairs</span>
    </div>
  </section>
</main>
</body>
</html>
```